Bry7Legal Letterhead

Need a new letterhead for my law firm.
IDENTIFYING INFORMATION BELOW:
Anselmo R Quintara III
Attorney at Law
Address: 2847 Larkspur Blvd, Ste 300, Dallas, TX 75204
Phone: 877-482-6017
Fax: 469-738-1452
Email: bry@bry7legal.example
Website: www.bry7legal.example

Colors
0054AA
0677BA
7BADD7
CADEEF
E8F1F8

Requirements
Must have
• Logo needs to be on the letterhead, along with identifying information which is included in the project description.

```html
<!DOCTYPE html>
<html lang="en">
<head>
<meta charset="utf-8">
<title>Bry7Legal Letterhead</title>
<link href="https://fonts.googleapis.com/css2?family=Arimo:wght@400;700&display=swap" rel="stylesheet">
<style>
  :root {
    --ink: #1a1a1a;
    --text: #4a4a4a;
    --blue: #0677BA;
    --blue-deep: #0054AA;
    --paper: #ffffff;
    --backdrop: #e9eaec;
    --band: #0b0b0b;
  }
  * { margin: 0; padding: 0; box-sizing: border-box; }
  html, body { width: 1200px; height: 795px; overflow: hidden; }
  body {
    background: var(--backdrop);
    font-family: "Arimo", Arial, sans-serif;
    color: var(--text);
  }
  .letterhead {
    position: absolute;
    left: 316px; top: 30px;
    width: 568px; height: 735px;
    background: var(--paper);
    box-shadow: 0 2px 10px rgba(0,0,0,.08);
    overflow: hidden;
  }
  .brand {
    position: absolute; top: 58px; left: 0; right: 0;
    text-align: center;
  }
  .brand-name {
    font-weight: 700; font-size: 24px; letter-spacing: 1px;
    color: var(--ink); text-transform: uppercase;
  }
  .brand-tagline {
    font-size: 7px; letter-spacing: 2.4px; color: var(--ink);
    text-transform: uppercase; margin-top: 2px;
  }
  .letter-body {
    position: absolute; top: 190px; left: 62px; width: 420px;
    font-size: 9px; line-height: 1.55;
  }
  .salutation { font-size: 11px; margin-bottom: 14px; color: var(--text); }
  .letter-body p { margin-bottom: 13px; }
  .closing { margin-top: 6px; }
  .signature {
    width: 90px; height: 40px; margin-top: 8px;
    background: linear-gradient(90deg, #e6e8ec, #d3d7de);
    border-radius: 3px;
  }
  .footer-rule {
    position: absolute; left: 62px; right: 60px; top: 622px;
    border-top: 1px solid var(--ink);
  }
  .signer { position: absolute; left: 62px; top: 604px; }
  .signer-name {
    font-weight: 700; font-size: 12.5px; color: var(--ink);
    text-transform: uppercase; letter-spacing: .2px;
  }
  .signer-title {
    position: absolute; left: 62px; top: 627px;
    font-size: 9.5px; color: var(--blue);
  }
  .contact-list {
    position: absolute; left: 62px; top: 650px;
    list-style: none; font-size: 9px; color: var(--ink); line-height: 1.5;
  }
  .contact-list li { display: flex; align-items: center; gap: 6px; }
  .contact-list svg { width: 8px; height: 8px; fill: var(--blue); }
  .address {
    position: absolute; right: 60px; top: 630px;
    text-align: right; font-size: 8.5px; line-height: 1.4; color: var(--ink);
  }
  .base-band { position: absolute; left: 0; bottom: 0; width: 568px; height: 30px; }
  .web-address {
    position: absolute; right: 14px; bottom: 9px;
    font-size: 8px; letter-spacing: 1.6px; color: #fff; text-transform: uppercase;
  }
</style>
</head>
<body>
<main class="letterhead">
  <header class="brand">
    <div class="brand-name">Bry7Legal</div>
    <div class="brand-tagline">Steady counsel</div>
  </header>

  <section class="letter-body">
    <div class="salutation">Dear Mr. Smith,</div>
    <p>Lorem ipsum dolor sit amet, consectetur adipiscing elit. Donec orci purus, luctus vitae dignissim eu, iaculis sed purus. Vivamus faucibus, ipsum nec aliquet viverra, leo mauris condimentum ligula, sit amet sagittis enim ligula quis arcu. Nam egestas tortor id nisl porttitor mattis. In tortor ante, ultricies in suscipit a, tempus non massa. Vivamus et auctor mi. Fusce vel massa nulla. Phasellus nec eros mauris, et scelerisque orci.</p>
    <p>Donec malesuada orci vitae nulla accumsan porta a id massa. Quisque accumsan iaculis magna sit amet fringilla. Maecenas consequat, magna eget tincidunt semper, odio nibh rutrum mi, id feugiat ante nisl eu risus. Vestibulum nunc orci, rhoncus a placerat in, ultricies in mi. Cras mattis varius eros, vel fringilla nisi suscipit eget. Quisque scelerisque sagittis nulla at porttitor.</p>
    <p>Sed id augue vitae urna euismod commodo aliquet a quam. Pellentesque arcu velit, cursus et malesuada ut, consequat et diam. Nullam erat sem, rhoncus id ullamcorper vitae, rhoncus et arcu. In ultricies ultricies nulla, ut rutrum nisl iaculis at. Donec eu magna a metus ornare faucibus. Fusce aliquet faucibus ultricies. Morbi semper, est id tincidunt gravida, sem arcu adipiscing lacus, ac bibendum nulla leo eu purus. Quisque nec diam sed risus consectetur accumsan quis quis nibh. Vestibulum id purus lorem.</p>
    <div class="closing">Sincerely,</div>
    <div class="signature" role="img" aria-label="Handwritten signature of the attorney"></div>
  </section>

  <div class="signer"><div class="signer-name">Anselmo R Quintara III</div></div>
  <div class="footer-rule"></div>
  <div class="signer-title">Attorney at Law</div>

  <ul class="contact-list">
    <li><svg viewBox="0 0 10 10"><path d="M2 0h2l1 3-1.5 1a6 6 0 0 0 2.5 2.5L7 5l3 1v2a2 2 0 0 1-2 2A8 8 0 0 1 0 2a2 2 0 0 1 2-2z"/></svg>877-482-6017</li>
    <li><svg viewBox="0 0 10 10"><path d="M2 0h5v3H2zM0 4h10v5H0zM2 7h6v3H2z"/></svg>469-738-1452</li>
    <li><svg viewBox="0 0 10 10"><path d="M0 2h10v6H0zM0 2l5 3.5L10 2v1L5 6.5 0 3z"/></svg>bry@bry7legal.example</li>
  </ul>

  <address class="address" style="font-style:normal">
    2847 Larkspur Blvd<br>Ste 300<br>Dallas, TX 75204
  </address>

  <svg class="base-band" viewBox="0 0 568 30" preserveAspectRatio="none">
    <rect x="0" y="22" width="568" height="8" fill="var(--band)"/>
    <polygon points="410,4 568,4 568,30 402,30" fill="var(--blue)"/>
  </svg>
  <div class="web-address">www.bry7legal.example</div>
</main>
</body>
</html>
```